Ward Compass Business Card Design*

We need a business card design for our company Ward Compass. Our company is specialized in providing online consulting services regarding medical institutions, hospitals and doctors. We work with patients worldwide looking to choose between healthcare providers. We have a website you may use as a reference, where we list doctors and clinics worldwide. So we target Medical providers as well as patients worldwide.
Target Market(s)
Medical Providers and patients around the world
Industry/Entity Type
Medical
Contact Information for Business Card
Salwa Kettani
CEO
+90 612 348 2175
info@wardcompass.example
www.wardcompass.example
14 Annakhil 7 H.R.B. Rabat, Morocco
Requirements
Must have
- Company logo/name on one full side, personal info and smaller logo and company name on the other side.
Nice to have
- Smart and elegant design

```html
<!DOCTYPE html>
<html lang="en">
<head>
<meta charset="utf-8">
<title>Ward Compass – Business Card</title>
<link rel="stylesheet" href="https://fonts.googleapis.com/css2?family=Montserrat:wght@400;600;700&family=Roboto:wght@400;500&display=swap">
<style>
  :root {
    --navy: #15396a;
    --navy-pattern: #1b4275;
    --grey-line: #808080;
    --white: #ffffff;
    --ink-soft: #4a4a4a;
    --page: #2b2d31;
  }
  * { box-sizing: border-box; margin: 0; padding: 0; }
  html, body { width: 1200px; height: 1000px; overflow: hidden; }
  body {
    background: var(--page);
    font-family: "Roboto", Arial, sans-serif;
    position: relative;
  }
  .card {
    position: absolute;
    left: 250px;
    width: 700px;
    height: 400px;
    border-radius: 22px;
    overflow: hidden;
  }
  .card--back { top: 70px; background: var(--navy); }
  .card--front { top: 530px; background: var(--white); }

  .pattern-field {
    position: absolute; inset: 0;
    background: linear-gradient(135deg, var(--navy) 0%, var(--navy-pattern) 50%, var(--navy) 100%);
  }
  .brand {
    position: absolute;
    display: flex;
    align-items: center;
    gap: 10px;
    font-family: "Montserrat", Arial, sans-serif;
    font-weight: 700;
    letter-spacing: 0.5px;
    white-space: nowrap;
  }
  .brand__dot { border-radius: 50%; flex: none; }
  .card--back .brand { right: 48px; bottom: 52px; color: var(--white); font-size: 24px; }
  .card--back .brand__dot { width: 22px; height: 22px; background: var(--white); }

  .front-shape { position: absolute; inset: 0; }
  .card--front .brand { left: 470px; top: 180px; color: var(--navy); font-size: 27px; flex-direction: column; align-items: flex-start; gap: 12px; }
  .card--front .brand__dot { width: 34px; height: 34px; background: var(--navy); }

  .person {
    position: absolute; left: 54px; top: 52px; color: var(--white);
  }
  .person__name { font-family: "Montserrat", Arial, sans-serif; font-weight: 600; font-size: 24px; letter-spacing: 0.5px; text-transform: uppercase; }
  .person__role { font-family: "Montserrat", Arial, sans-serif; font-weight: 600; font-size: 21px; margin-top: 4px; }

  .contact {
    position: absolute; left: 54px; top: 168px; color: var(--white);
    font-size: 16px; line-height: 1.35; list-style: none;
  }
  .contact__address { margin-bottom: 18px; }
  .contact__item { display: flex; align-items: center; gap: 10px; margin-bottom: 8px; }
  .contact__icon { width: 14px; height: 14px; flex: none; }
</style>
</head>
<body>

<section class="card card--back" aria-label="Card back">
  <div class="pattern-field" role="img" aria-label="Faint repeating brand monogram pattern on navy"></div>
  <div class="brand"><span class="brand__dot"></span>Ward Compass</div>
</section>

<section class="card card--front" aria-label="Card front">
  <svg class="front-shape" width="700" height="400" viewBox="0 0 700 400" aria-hidden="true">
    <path d="M0 0 H430 Q330 200 480 400 H0 Z" fill="var(--navy)"/>
    <path d="M444 -2 Q346 200 494 402" fill="none" stroke="var(--grey-line)" stroke-width="6"/>
  </svg>

  <div class="person">
    <p class="person__name">Salwa Kettani</p>
    <p class="person__role">CEO</p>
  </div>

  <ul class="contact">
    <li class="contact__address">14 Annakhil 7 H.R.B.<br>Rabat, Morocco</li>
    <li class="contact__item">
      <svg class="contact__icon" viewBox="0 0 24 24" aria-hidden="true"><path fill="#fff" d="M6.6 10.8a15 15 0 0 0 6.6 6.6l2.2-2.2a1 1 0 0 1 1-.25 11.4 11.4 0 0 0 3.6.57 1 1 0 0 1 1 1V20a1 1 0 0 1-1 1A17 17 0 0 1 3 4a1 1 0 0 1 1-1h3.5a1 1 0 0 1 1 1c0 1.25.2 2.45.57 3.57a1 1 0 0 1-.25 1z"/></svg>
      +90 612 348 2175
    </li>
    <li class="contact__item">
      <svg class="contact__icon" viewBox="0 0 24 24" aria-hidden="true"><path fill="#fff" d="M2 5h20v14H2z M4 7v.5l8 5 8-5V7l-8 5z" fill-rule="evenodd"/></svg>
      info@wardcompass.example
    </li>
    <li class="contact__item">
      <svg class="contact__icon" viewBox="0 0 24 24" aria-hidden="true"><circle cx="12" cy="12" r="10" fill="none" stroke="#fff" stroke-width="2"/><path d="M2 12h20M12 2c3 3 3 17 0 20M12 2c-3 3-3 17 0 20" fill="none" stroke="#fff" stroke-width="1.6"/></svg>
      www.wardcompass.example
    </li>
  </ul>

  <div class="brand"><span class="brand__dot"></span>Ward Compass</div>
</section>

</body>
</html>
```